Floravine Pte Ltd

I want a creative and stand out web page so when my client search for my web page or google search. The front page is stand out and they know that we are the interior office designer that are searching for . We are commercial office design company. We also have the video to put at our front page for client to see. Natural is the key elements. As we like to carry recycle materials , plant , trees is our key element such as biophilic design
Updates

Hi All,

For my web page, I need minimalist design and creative frontpage.
When my client search for my web page, they straight feel that this is the office design company.
The webpage is special and nature is the key element for the design.
My company logo can be design in the shaped of the letter OO in the webpage.
Below is the sample you can refer.

https://www.pinboardly.example/pin/527190364821057392/

Target Market(s)

Customer searching for office design

Industry/Entity Type

Commerical designer firm- Office interior design & Build company

Number of Pages Required

5+ page

Font styles to use
Other font styles liked:
• Wilmina

Colors
59FF00
82FF00
B8FF75
E3FFCB
F4FFEA
FFC000
F8CF3A
FAE287
FDF2CF
FEFAEE
6B429C
8869AF
B7A5CE
E3DAEB
F3F0F8

Requirements
Must have
• Home, Services,Gallery, Calculator, Testimonials, Contact, Blog
Nice to have
• Natural, creative, minimalist
Should not have
• No black color or blue color

```html
<!DOCTYPE html>
<html lang="en">
<head>
<meta charset="utf-8">
<title>Floravine Pte Ltd — Office Interior Design &amp; Build</title>
<link href="https://fonts.googleapis.com/css2?family=Poppins:wght@400;500;600;700&family=Questrial&display=swap" rel="stylesheet">
<style>
:root{
  --green:#82FF00;
  --green-bright:#59FF00;
  --green-pale:#F4FFEA;
  --green-soft:#E3FFCB;
  --purple:#6B429C;
  --purple-mid:#8869AF;
  --orange:#F05A28;
  --gold:#F8CF3A;
  --ink:#2b2b2b;
  --text:#444;
  --white:#fff;
  --footer:#1f1f1f;
  --footer-bar:#2a2a2a;
}
*{box-sizing:border-box;margin:0;padding:0}
html,body{width:1200px;height:4269px;overflow:hidden}
body{font-family:'Poppins',sans-serif;color:var(--text);background:var(--white);position:relative}
section,header,footer{position:absolute;left:0;width:1200px}
.abs{position:absolute}
.heading{font-family:'Questrial',sans-serif;color:var(--purple);font-size:35px;letter-spacing:.5px;text-transform:uppercase;font-weight:400}
.center{left:0;width:1200px;text-align:center}

/* Header */
.site-header{top:0;height:78px;background:var(--white);box-shadow:0 1px 4px rgba(0,0,0,.06)}
.brand{left:110px;top:16px;display:flex;align-items:center;gap:6px}
.brand-dot{width:14px;height:14px;border-radius:50%;border:3px solid var(--orange)}
.brand-name{font-family:'Poppins',sans-serif;font-size:14px;color:var(--orange);font-weight:400}
.main-nav{right:110px;top:27px;display:flex;gap:32px}
.main-nav a{font-size:15px;font-weight:600;color:var(--ink);text-decoration:none}
.main-nav a.active{color:var(--orange)}

/* Hero */
.hero{top:78px;height:522px;background:linear-gradient(180deg,#4a5a46 0%,#33412f 45%,#26331f 100%)}
.hero-media{position:absolute;inset:0;background:linear-gradient(120deg,rgba(80,100,110,.55),rgba(40,60,30,.7) 60%,rgba(30,45,25,.85))}
.hero-title{top:135px;font-family:'Questrial',sans-serif;color:var(--white);font-size:30px;line-height:57px;text-transform:uppercase;letter-spacing:.3px}
.play{left:578px;top:334px}
.hero-social{left:1136px;top:381px;display:flex;flex-direction:column;gap:20px}
.hero-social span{width:14px;height:14px;border-radius:50%;background:var(--white)}

/* About */
.about{top:600px;height:676px}
.about .heading{left:107px;top:86px}
.about-text{left:109px;top:160px;width:490px;font-size:17px;line-height:32.5px;color:#333}
.about-text p+p{margin-top:22px}
.btn-read{left:113px;top:518px;width:131px;height:39px;background:var(--green);color:var(--purple);font-size:14px;font-weight:700;display:flex;align-items:center;justify-content:center;text-decoration:none}
.dots{width:56px;height:325px;background-image:radial-gradient(circle,var(--green) 1.6px,transparent 1.8px);background-size:14px 14.5px}
.about-photo{left:759px;top:93px;width:330px;height:465px;background:linear-gradient(160deg,#6e5a3a,#3f4a2a 45%,#7b8a52 70%,#4a3a26)}

/* Awards */
.awards{top:1276px;height:469px;background:var(--green-pale)}
.awards .heading{top:88px}
.arrow{font-size:22px;color:var(--ink)}

/* Services */
.services{top:1745px;height:1039px}
.services-intro{left:103px;top:160px;width:315px;text-align:center}
.services-intro .heading{font-size:34px}
.services-intro p{margin-top:24px;font-size:15px;line-height:30px;color:#333}
.card{width:303px;height:376px;background:var(--white);box-shadow:0 2px 10px rgba(0,0,0,.1);text-align:center;padding:13px}
.card.highlight{background:var(--green-pale)}
.card-media{height:122px;width:100%}
.card h3{margin-top:36px;font-size:14px;font-weight:400;text-transform:uppercase;color:#333}
.card p{margin-top:14px;font-size:15px;line-height:30px;color:#333;padding:0 8px}
.card .learn{display:inline-block;margin-top:10px;font-size:15px;font-weight:600;color:var(--purple-mid);text-decoration:underline}

/* Portfolio */
.portfolio{top:2784px;height:616px;background:var(--green-pale)}
.portfolio .heading{top:85px}
.project-media{top:174px;height:298px}
.project-name{top:490px;font-size:17px;font-weight:700;color:var(--ink);text-transform:uppercase;white-space:nowrap}

/* Partners */
.partners{top:3400px;height:486px;background:linear-gradient(160deg,#fbfbfb,#f1f1f1)}
.partners .heading{top:103px}

/* Footer */
.site-footer{top:3886px;height:310px;background:var(--footer)}
.footer-brand{left:0;width:1200px;top:70px;display:flex;justify-content:center;align-items:center;gap:10px}
.footer-brand .brand-dot{border-color:var(--white);width:20px;height:20px}
.footer-brand .brand-name{color:var(--white);font-size:20px}
.footer-nav{left:0;width:1200px;top:170px;display:flex;justify-content:center;gap:32px}
.footer-nav a{color:var(--white);font-size:15px;font-weight:600;text-decoration:none}
.footer-social{left:0;width:1200px;top:230px;display:flex;justify-content:center;gap:22px}
.footer-social span{width:13px;height:13px;border-radius:50%;background:var(--white)}
.chat{left:1084px;top:63px}
.footer-bar{top:4196px;height:73px;background:var(--footer-bar);color:var(--white);font-size:14px}
.footer-bar .copy{left:106px;top:26px}
.footer-bar .code{left:1050px;top:26px}
</style>
</head>
<body>

<header class="site-header">
  <div class="brand abs"><span class="brand-dot"></span><span class="brand-name">Floravine Pte Ltd</span></div>
  <nav class="main-nav abs">
    <a class="active" href="#">Home</a><a href="#">Services</a><a href="#">Gallery</a><a href="#">Calculator</a><a href="#">Testimonials</a><a href="#">Contact</a><a href="#">Blog</a><a href="#">Portfolio</a>
  </nav>
</header>

<section class="hero">
  <div class="hero-media" role="img" aria-label="Glass office tower wrapped in lush green trees"></div>
  <h1 class="hero-title abs center">Bring goods straight from<br>factory &amp; cut away the middleman costing so client can<br>have a better quality with affordable price.</h1>
  <svg class="play abs" width="44" height="44" viewBox="0 0 44 44" aria-label="Play video"><circle cx="22" cy="22" r="20" fill="none" stroke="#fff" stroke-width="2"/><path d="M18 14 L30 22 L18 30 Z" fill="none" stroke="#fff" stroke-width="2" stroke-linejoin="round"/></svg>
  <div class="hero-social abs"><span></span><span></span><span></span></div>
</section>

<section class="about">
  <h2 class="heading abs">About Floravine</h2>
  <div class="about-text abs">
    <p>Floravine is an interior design and renovation company that specialises in office interior design and commercial retail renovation. We always aim to provide premium quality services with competitive cost and ensuring our clients are pleased with the outcome.</p>
    <p>Since 2010 when the firm began, Floravine has amassed a wealth of experience in commercial interior design. Our team of dedicated and professional designers is committed to creating</p>
  </div>
  <a class="btn-read abs" href="#">READ MORE</a>
  <div class="dots abs" style="left:671px;top:162px"></div>
  <div class="dots abs" style="left:1113px;top:162px"></div>
  <div class="about-photo abs" role="img" aria-label="Multi-level office atrium filled with hanging plants and warm lighting"></div>
</section>

<section class="awards">
  <h2 class="heading abs center">Awards</h2>
  <span class="arrow abs" style="left:155px;top:248px">&#8249;</span>
  <span class="arrow abs" style="left:1032px;top:248px">&#8250;</span>
  <svg class="abs" style="left:0;top:180px" width="1200" height="160" aria-label="Award badges">
    <circle cx="292" cy="75" r="62" fill="#C9A24A"/>
    <rect x="449" y="18" width="110" height="115" rx="10" fill="#D9B46A"/>
    <circle cx="709" cy="72" r="56" fill="#BFA36A"/>
    <rect x="856" y="22" width="110" height="110" rx="55" fill="var(--gold)"/>
  </svg>
</section>

<section class="services">
  <div class="services-intro abs">
    <h2 class="heading">Our Services</h2>
    <p>For Floravine, design has no limit and value. We constantly strive to make sure that our clients get the best. services possible. We offer our services to corporate and commercial industries including food and beverage, retail, education, government and hospitality to name a few.</p>
  </div>

  <article class="card abs" style="left:446px;top:129px">
    <div class="card-media" role="img" aria-label="Covered walkway lined with green vertical planting" style="background:linear-gradient(135deg,#7aa84a,#b8d58a 50%,#5d7f3a)"></div>
    <h3>Pre-lease service</h3>
    <p>It can be rather tedious and challenging to find the perfect office space that will suit your unique needs and concerns.</p>
  </article>
  <article class="card highlight abs" style="left:780px;top:129px">
    <div class="card-media" role="img" aria-label="Open office lounge with arched windows and planters" style="background:linear-gradient(135deg,#9a8a6a,#c9b890 50%,#6b7a4a)"></div>
    <h3>Interior design &amp; planning</h3>
    <p>We understand the importance of having a conducive environment to support your company's day-to-day operations.</p>
    <a class="learn" href="#">LEARN MORE</a>
  </article>
  <article class="card abs" style="left:108px;top:552px">
    <div class="card-media" role="img" aria-label="Bright lobby with indoor garden beds" style="background:linear-gradient(135deg,#5a5f55,#a9b2a0 50%,#4d5a3d)"></div>
    <h3>Engineering services</h3>
    <p>Our company can design electrical and mechanical systems, which work seamlessly with building provisions that ad-</p>
  </article>
  <article class="card abs" style="left:446px;top:552px">
    <div class="card-media" role="img" aria-label="Workstations beneath a living green wall" style="background:linear-gradient(135deg,#4f6b35,#93ad6a 50%,#b9b4a4)"></div>
    <h3>Procurement &amp; construction</h3>
    <p>Another part of our services include the procurement and construction. We understand how complicated it can be to</p>
  </article>
  <article class="card abs" style="left:780px;top:552px">
    <div class="card-media" role="img" aria-label="Meeting area with timber panels and moss walls" style="background:linear-gradient(135deg,#3f4a35,#6f8f45 50%,#8a6a48)"></div>
    <h3>Migration management</h3>
    <p>We realize the importance of continuous checks on your project even long after its construction. Hence, you can count</p>
  </article>
</section>

<section class="portfolio">
  <h2 class="heading abs center">Portfolio</h2>
  <div class="project-media abs" style="left:0;width:311px;background:linear-gradient(135deg,#b88a2a,#e3c46a 60%,#c9a04a)" role="img" aria-label="Reception counter with gold quilted wall"></div>
  <div class="project-name abs" style="left:-6px">Suryadana Holdings</div>
  <div class="project-media abs" style="left:360px;width:482px;background:linear-gradient(135deg,#7a3a24,#b5693c 45%,#3b2a20)" role="img" aria-label="Restaurant dining room with brick walls and pendant lamps"></div>
  <div class="project-name abs" style="left:360px;width:482px;text-align:center">Lemongrass Thai Kitchen</div>
  <div class="project-media abs" style="left:890px;width:310px;background:linear-gradient(135deg,#e8eaee,#cfd5de 60%,#9fb0c8)" role="img" aria-label="White corporate showroom with curved ceiling feature"></div>
  <div class="project-name abs" style="left:1031px">Meridian Asia Pacific</div>
</section>

<section class="partners">
  <h2 class="heading abs center">Our Partnets</h2>
  <span class="arrow abs" style="left:160px;top:284px">&#8249;</span>
  <span class="arrow abs" style="left:1037px;top:284px">&#8250;</span>
  <svg class="abs" style="left:0;top:240px" width="1200" height="130" aria-label="Partner badges">
    <circle cx="316" cy="62" r="60" fill="#2f4a44"/>
    <circle cx="524" cy="62" r="52" fill="#9bd12e"/>
    <rect x="669" y="10" width="104" height="104" rx="8" fill="#c6d93a"/>
    <rect x="855" y="18" width="90" height="90" rx="6" fill="#f39a1e"/>
  </svg>
</section>

<footer class="site-footer">
  <div class="footer-brand abs"><span class="brand-dot"></span><span class="brand-name">Floravine Pte Ltd</span></div>
  <nav class="footer-nav abs">
    <a href="#">Home</a><a href="#">Services</a><a href="#">Gallery</a><a href="#">Calculator</a><a href="#">Testimonials</a><a href="#">Contact</a><a href="#">Blog</a><a href="#">Portfolio</a>
  </nav>
  <div class="footer-social abs"><span></span><span></span><span></span><span></span><span></span></div>
  <svg class="chat abs" width="52" height="52" viewBox="0 0 52 52" aria-label="Chat"><path d="M26 6c12 0 22 8 22 18s-10 18-22 18c-3 0-6-.5-8-1.3L8 45l3-9C7 32 4 28 4 24 4 14 14 6 26 6z" fill="#fff"/><circle cx="17" cy="24" r="3" fill="var(--footer)"/><circle cx="26" cy="24" r="3" fill="var(--footer)"/><circle cx="35" cy="24" r="3" fill="var(--footer)"/></svg>
</footer>
<div class="footer-bar abs" style="left:0;width:1200px">
  <span class="copy abs">© 2023 floravine pte ltd</span>
  <span class="code abs">C64</span>
</div>

</body>
</html>
```